New website for concierge mobile medical service

new website for business:
WEBSITE REQUEST LIST:
Luxury product look.
Professional. Clean & simple, NO stock people photos. Graphics OK.
Black and white text.

```html
<!DOCTYPE html>
<html lang="en">
<head>
<meta charset="utf-8">
<title>Lumen Care — Pricing</title>
<link rel="stylesheet" href="https://fonts.googleapis.com/css2?family=Lato:wght@400;700;900&family=Fira+Sans:wght@400;500;600&display=swap">
<style>
  :root {
    --ink: #1d1d1f;
    --white: #ffffff;
    --purple: #5c5aa8;
    --navy: #0b2236;
    --hero-dark: #04121c;
    --hero-blue: #0d3f63;
    --card-top: #3f57a6;
    --card-bottom: #8b79b9;
    --btn-top: #0b2434;
    --btn-bottom: #0f4a5e;
    --band-left: #1b7f9a;
    --band-right: #1a8aa8;
    --cta: #88cfd6;
    --footer: #1e1e1e;
  }
  * { box-sizing: border-box; margin: 0; padding: 0; }
  html, body { width: 1123px; height: 1200px; overflow: hidden; }
  body { position: relative; background: var(--white); font-family: 'Lato', sans-serif; color: var(--ink); }

  .site-header { position: absolute; left: 0; top: 0; width: 1123px; height: 100px; background: var(--white); }
  .brand { position: absolute; left: 150px; top: 40px; display: flex; align-items: center; gap: 10px; }
  .brand-dot { width: 34px; height: 34px; border-radius: 50%; background: var(--navy); }
  .brand-name { font-family: 'Lato', sans-serif; font-weight: 700; font-size: 24px; color: var(--navy); }
  .phone { position: absolute; left: 831px; top: 15px; display: flex; align-items: center; gap: 12px; }
  .phone-icon { width: 30px; height: 30px; background: var(--purple); border-radius: 2px; display: flex; align-items: center; justify-content: center; }
  .phone-number { font-weight: 700; font-size: 18px; color: var(--purple); }
  .main-nav { position: absolute; right: 134px; top: 70px; display: flex; gap: 0; }
  .main-nav a { position: relative; font-weight: 700; font-size: 11.5px; color: var(--ink); text-decoration: none; padding: 0 0 0 37px; line-height: 16px; }
  .main-nav a.active::after { content: ""; position: absolute; left: 29px; right: -8px; top: 25px; height: 5px; background: var(--navy); }

  .hero { position: absolute; left: 0; top: 100px; width: 1123px; height: 248px;
    background: radial-gradient(ellipse at 85% 60%, #0f5a86 0%, transparent 45%), linear-gradient(90deg, var(--hero-dark) 0%, #072338 50%, var(--hero-blue) 100%); }
  .hero-title { position: absolute; left: 135px; top: 96px; font-weight: 900; font-size: 42px; color: var(--white); letter-spacing: 0.5px; }

  .intro { position: absolute; left: 0; top: 388px; width: 1123px; text-align: center; font-size: 14.5px; line-height: 25px; color: var(--ink); }

  .plan { position: absolute; top: 462px; width: 268px; height: 307px; border-radius: 3px; color: var(--white); text-align: center;
    background: linear-gradient(180deg, var(--card-top) 0%, var(--card-bottom) 100%); font-family: 'Fira Sans', sans-serif; }
  .plan-title { margin-top: 16px; font-size: 23px; font-weight: 500; letter-spacing: 0.3px; }
  .plan-icon { width: 44px; height: 44px; margin: 10px auto 0; border-radius: 6px; background: rgba(255,255,255,0.9); }
  .plan-price { margin-top: 10px; font-size: 39px; font-weight: 600; line-height: 44px; }
  .plan-price sup { font-size: 18px; vertical-align: 16px; }
  .plan-price small { font-size: 19px; }
  .plan-features { list-style: none; margin-top: 6px; font-family: 'Lato', sans-serif; font-size: 13.5px; line-height: 27.7px; }
  .plan-button { position: absolute; left: 24px; top: 284px; width: 220px; height: 44px; line-height: 44px;
    background: linear-gradient(180deg, var(--btn-top), var(--btn-bottom)); color: var(--white); font-size: 16.5px; font-weight: 500; text-decoration: none; }

  .subscribe { position: absolute; left: 0; top: 838px; width: 1123px; height: 235px;
    background: linear-gradient(120deg, var(--band-left) 0%, #237f9b 50%, var(--band-right) 100%); }
  .subscribe-title { position: absolute; left: 0; width: 1123px; top: 38px; text-align: center; font-family: 'Fira Sans', sans-serif; font-weight: 500; font-size: 30px; color: var(--white); }
  .field { position: absolute; top: 97px; width: 298px; height: 40px; background: var(--white); font-size: 12px; padding-left: 14px; line-height: 40px; color: var(--ink); }
  .subscribe-button { position: absolute; left: 258px; top: 146px; width: 607px; height: 42px; background: var(--cta); color: var(--white); text-align: center; line-height: 42px; font-weight: 700; font-size: 14px; }

  .site-footer { position: absolute; left: 0; top: 1073px; width: 1123px; height: 127px; background: var(--footer); color: var(--white); text-align: center; }
  .footer-nav { display: flex; justify-content: center; gap: 37px; margin-top: 23px; }
  .footer-nav a { color: var(--white); text-decoration: none; font-weight: 700; font-size: 11.5px; }
  .copyright { margin-top: 17px; font-size: 10.5px; }
  .social { display: flex; justify-content: center; gap: 16px; margin-top: 14px; }
  .social span { width: 16px; height: 16px; border-radius: 50%; background: var(--white); }
</style>
</head>
<body>
  <header class="site-header">
    <div class="brand"><span class="brand-dot"></span><span class="brand-name">Lumen Care</span></div>
    <div class="phone">
      <span class="phone-icon">
        <svg width="16" height="16" viewBox="0 0 24 24" aria-hidden="true"><path fill="#fff" d="M6.6 10.8a15.1 15.1 0 0 0 6.6 6.6l2.2-2.2a1 1 0 0 1 1-.25 11.4 11.4 0 0 0 3.6.57 1 1 0 0 1 1 1V20a1 1 0 0 1-1 1A17 17 0 0 1 3 4a1 1 0 0 1 1-1h3.5a1 1 0 0 1 1 1c0 1.25.2 2.45.57 3.57a1 1 0 0 1-.25 1z"/></svg>
      </span>
      <span class="phone-number">555-014-2200</span>
    </div>
    <nav class="main-nav">
      <a href="#">HOME</a><a href="#">ABOUT US</a><a href="#">WHY LUMEN?</a><a href="#">SERVICE AREA</a><a href="#" class="active">OTHER</a><a href="#">FAQ</a><a href="#">CONTACT US</a>
    </nav>
  </header>

  <section class="hero" role="img" aria-label="Dark blue banner with glowing circular medical icons: heart rate, lab flask, brain, eye, hospital bed">
    <h1 class="hero-title">PRICING</h1>
  </section>

  <p class="intro">Now accepting new patients with full mobile care starting March 1, 2020<br>New patients will have immediate access to Lumen Care mobile urgent care for $50/month.</p>

  <article class="plan" style="left:136px">
    <h2 class="plan-title">Individual</h2>
    <div class="plan-icon" role="img" aria-label="Single person icon"></div>
    <div class="plan-price"><sup>$</sup>300/<small>mo.</small></div>
    <ul class="plan-features"><li>Sed scelerisque sem</li><li>Purus bibendumeu varius</li><li>Enim imperdiet</li><li>Phasellus a ipsum</li></ul>
    <a class="plan-button" href="#">Subscribe Today</a>
  </article>
  <article class="plan" style="left:428px">
    <h2 class="plan-title">Married Couple</h2>
    <div class="plan-icon" role="img" aria-label="Couple icon"></div>
    <div class="plan-price"><sup>$</sup>400/<small>mo.</small></div>
    <ul class="plan-features"><li>Sed scelerisque sem</li><li>Purus bibendumeu varius</li><li>Enim imperdiet</li><li>Phasellus a ipsum</li></ul>
    <a class="plan-button" href="#">Subscribe Today</a>
  </article>
  <article class="plan" style="left:721px">
    <h2 class="plan-title">Child with Adult</h2>
    <div class="plan-icon" role="img" aria-label="Adult with child icon"></div>
    <div class="plan-price"><sup>$</sup>75/<small>ea.mo.</small></div>
    <ul class="plan-features"><li>Sed scelerisque sem</li><li>Purus bibendumeu varius</li><li>Enim imperdiet</li><li>Phasellus a ipsum</li></ul>
    <a class="plan-button" href="#">Subscribe Today</a>
  </article>

  <section class="subscribe" role="img" aria-label="Teal background with faint hexagon and medical symbol pattern">
    <h2 class="subscribe-title">Subscribe</h2>
    <div class="field" style="left:258px">Enter Name</div>
    <div class="field" style="left:568px">Enter Email Address</div>
    <div class="subscribe-button">SUBSCRIBE NOW</div>
  </section>

  <footer class="site-footer">
    <nav class="footer-nav">
      <a href="#">HOME</a><a href="#">ABOUT US</a><a href="#">WHY LUMEN?</a><a href="#">SERVICE AREA</a><a href="#">OTHER</a><a href="#">CONTACT US</a>
    </nav>
    <p class="copyright">Copyright © 2019. Company Name All Rights Reserved</p>
    <div class="social" aria-label="Social links"><span></span><span></span><span></span><span></span><span></span></div>
  </footer>
</body>
</html>
```